Vantrel Intergrated Marketing Stationary Design Contest

We require a very professional looking stationary set to include: letterhead, compliments slip and business cards (double sided bus cards).

Files should be supplied on either Illustrator or InDesign.

We are interested in perhaps encorporating a faint watermark with the letter q or the logo, but it isnt a pre-requisite

Target Market(s)

Business owners seeking professional marketing services

Industry/Entity Type

Marketing

Requirements
Must have
• Concurrent theme wiht business cards, letterhead and comp slip. Must be an editable document for future ammendment
Should not have
• No use of times new roman or similar fonts

```html
<!DOCTYPE html>
<html lang="en">
<head>
<meta charset="utf-8">
<title>Vantrel Integrated Marketing – Stationery Set</title>
<link rel="stylesheet" href="https://fonts.googleapis.com/css2?family=Source+Sans+3:ital,wght@0,400;0,600;0,700;1,400;1,600&display=swap">
<style>
  :root {
    --brand-orange: #f05a28;
    --brand-peach: #f6b595;
    --ink: #1a1a1a;
    --wordmark-grey: #3a3a3a;
    --paper: #ffffff;
    --edge: #222222;
  }
  * { box-sizing: border-box; margin: 0; padding: 0; }
  html, body { width: 1200px; height: 1200px; overflow: hidden; background: var(--paper); }
  body { position: relative; font-family: "Source Sans 3", Arial, sans-serif; color: var(--ink); }

  .sheet { position: absolute; background: var(--paper); border: 1px solid var(--edge); overflow: hidden; }
  .letterhead { left: 200px; top: 60px; width: 600px; height: 848px; }
  .comp-slip { left: 350px; top: 348px; width: 600px; height: 282px; }
  .card-front { left: 248px; top: 959px; width: 256px; height: 157px; }
  .card-back { left: 548px; top: 959px; width: 257px; height: 157px; }

  .wordmark { position: absolute; display: flex; align-items: center; gap: 6px; }
  .wordmark .dot { width: 22px; height: 22px; border-radius: 50%; background: var(--brand-orange); flex: none; }
  .wordmark .name { font-weight: 400; color: var(--wordmark-grey); font-size: 26px; letter-spacing: 3px; line-height: 1; }
  .wordmark.small .dot { width: 14px; height: 14px; }
  .wordmark.small .name { font-size: 16px; letter-spacing: 2px; }

  .letterhead .wordmark { left: 236px; top: 34px; }
  .comp-slip .wordmark { left: 224px; top: 20px; }
  .slip-title { position: absolute; left: 262px; top: 55px; color: var(--brand-peach); font-style: italic; font-weight: 600; font-size: 12px; }

  .footer { position: absolute; left: 0; right: 0; text-align: center; font-size: 7.5px; line-height: 10.5px; }
  .letterhead .footer { top: 826px; transform: translateY(-100%); }
  .letterhead .footer { top: 767px; transform: none; }
  .comp-slip .footer { top: 225px; }
  .footer .firm { color: var(--brand-orange); font-weight: 700; }
  .footer .office { font-style: italic; }
  .footer .label { color: var(--brand-orange); font-weight: 600; }
  .footer .gap { display: inline-block; width: 8px; }
  .footer .wide-gap { display: inline-block; width: 16px; }

  .card-front .wordmark { left: 12px; top: 72px; }
  .card-details { position: absolute; left: 122px; top: 37px; font-size: 5.5px; line-height: 7px; }
  .card-details .person { color: var(--brand-orange); font-weight: 700; font-size: 10px; line-height: 10px; }
  .card-details .role { font-weight: 600; font-size: 6px; margin-bottom: 8px; }
  .card-details .firm { color: var(--brand-orange); font-weight: 600; }
  .card-details .office { font-style: italic; }
  .card-details .contacts { margin-top: 6px; }
  .card-details .label { color: var(--brand-orange); font-weight: 600; }

  .card-back .wordmark { left: 26px; top: 72px; }
  .card-back .accent { position: absolute; left: 128px; top: -18px; width: 190px; height: 190px; border-radius: 50%; background: var(--brand-peach); }
</style>
</head>
<body>

<section class="sheet letterhead" aria-label="Letterhead">
  <div class="wordmark"><span class="dot"></span><span class="name">vantrel</span></div>
  <div class="footer">
    <div class="firm">Vantrel Integrated Marketing</div>
    <div class="office">Central Offices</div>
    <div>Larch Row, Brackenfield, North Wexmoor, WX7 4QP</div>
    <div><span class="label">W:</span> www.vantrelim.co.uk<span class="gap"></span><span class="label">E:</span> enquiries@vantrelim.co.uk<span class="gap"></span><span class="label">T:</span> 01632 960418<span class="gap"></span><span class="label">F:</span> 01632 960427</div>
    <div>Company registration: 4817306<span class="gap"></span>Vat No: 318 5274 60<span class="gap"></span>Trading as a division of Harrowell Ltd</div>
  </div>
</section>

<section class="sheet comp-slip" aria-label="Compliments slip">
  <div class="wordmark"><span class="dot"></span><span class="name">vantrel</span></div>
  <div class="slip-title">WITH COMPLEMENTS</div>
  <div class="footer">
    <div class="firm">Vantrel Integrated Marketing</div>
    <div class="office">Central Offices</div>
    <div>Larch Row, Brackenfield, North Wexmoor, WX7 4QP</div>
    <div><span class="label">W:</span> www.vantrelim.co.uk<span class="gap"></span><span class="label">E:</span> enquiries@vantrelim.co.uk<span class="gap"></span><span class="label">T:</span> 01632 960418<span class="gap"></span><span class="label">F:</span> 01632 960427</div>
    <div>Company registration: 4817307<span class="wide-gap"></span>Vat No: 318 5274 60<span class="gap"></span>Trading as a division of Harrowell Ltd</div>
  </div>
</section>

<section class="sheet card-front" aria-label="Business card front">
  <div class="wordmark small"><span class="dot"></span><span class="name">vantrel</span></div>
  <div class="card-details">
    <div class="person">Morven Haldane</div>
    <div class="role">General Manager</div>
    <div class="firm">Vantrel Integrated Marketing</div>
    <div class="office">Central Offices</div>
    <div>Larch Row, Brackenfield, North Wexmoor</div>
    <div>WX7 4QP</div>
    <div class="contacts">
      <div><span class="label">W:</span> www.vantrelim.co.uk</div>
      <div><span class="label">E:</span> morven@vantrelim.co.uk</div>
      <div><span class="label">T:</span> 01632 960418</div>
      <div><span class="label">F:</span> 01632 960427</div>
    </div>
  </div>
</section>

<section class="sheet card-back" aria-label="Business card back">
  <div class="accent"></div>
  <div class="wordmark small"><span class="name">vantrel</span></div>
</section>

</body>
</html>
```